Business card for medical clinic

I need an upmarket, modern medical/health business card for my clinic

Contact Information for Business Card

name, address, email, qr code

```html
<!DOCTYPE html>
<html lang="en">
<head>
<meta charset="utf-8">
<title>Meridian Care Clinic – Business Card</title>
<link href="https://fonts.googleapis.com/css2?family=Cinzel:wght@400;600&family=Arimo:wght@400&display=swap" rel="stylesheet">
<style>
  :root {
    --backdrop: #3d3d3d;
    --navy: #1a2a4e;
    --blue-glow: #08a6e6;
    --blue-mid: #0b6fb0;
    --white: #ffffff;
    --ink-blue: #1f5f9a;
    --rule-blue: #2a8fd0;
  }
  * { box-sizing: border-box; margin: 0; padding: 0; }
  html, body {
    width: 1200px; height: 803px; overflow: hidden;
    background: var(--backdrop);
  }
  .canvas { position: relative; width: 1200px; height: 803px; }

  .card {
    position: absolute;
    width: 460px; height: 263px;
    border-radius: 18px;
    overflow: hidden;
    box-shadow: 0 14px 30px rgba(0,0,0,.45);
  }
  .card--front-white { left: 120px; top: 90px; background: var(--white); }
  .card--contact {
    left: 620px; top: 90px;
    background: radial-gradient(ellipse 60% 75% at 45% 45%, var(--blue-glow) 0%, var(--blue-mid) 35%, var(--navy) 85%);
  }
  .card--front-blue {
    left: 370px; top: 440px;
    background: radial-gradient(ellipse 60% 75% at 40% 55%, var(--blue-glow) 0%, var(--blue-mid) 35%, var(--navy) 85%);
  }

  .brand {
    position: absolute; left: 0; right: 0; top: 50%;
    transform: translateY(-50%);
    display: flex; align-items: center; justify-content: center; gap: 14px;
  }
  .brand__dot {
    width: 16px; height: 16px; border-radius: 50%;
    flex: none;
  }
  .brand__name {
    font-family: "Cinzel", serif;
    font-weight: 600;
    font-size: 27px;
    letter-spacing: 1px;
    white-space: nowrap;
  }
  .card--front-white .brand__dot { background: var(--rule-blue); }
  .card--front-white .brand__name { color: var(--ink-blue); }
  .card--front-blue .brand__dot { background: var(--white); }
  .card--front-blue .brand__name { color: var(--white); }

  .contact {
    position: absolute; left: 92px; top: 52px;
    color: var(--white);
    font-family: "Arimo", sans-serif;
  }
  .contact__name {
    font-family: "Cinzel", serif;
    font-size: 24px; font-weight: 400; letter-spacing: 1px;
    line-height: 1;
  }
  .contact__role { font-size: 12px; margin-top: 3px; }
  .contact__address { font-size: 12.5px; line-height: 1.35; margin-top: 14px; }
  .contact__list { list-style: none; margin-top: 12px; font-size: 12.5px; line-height: 1.4; }
  .contact__list li { display: flex; align-items: center; gap: 8px; }
  .contact__list svg { width: 11px; height: 11px; flex: none; }
</style>
</head>
<body>
<main class="canvas">

  <section class="card card--front-white" aria-label="Card front, light">
    <div class="brand">
      <span class="brand__dot"></span>
      <span class="brand__name">Meridian Care Clinic</span>
    </div>
  </section>

  <section class="card card--contact" aria-label="Card back, contact details">
    <div class="contact">
      <p class="contact__name">Daniel Hart</p>
      <p class="contact__role">President</p>
      <p class="contact__address">412 Alder Court<br>Fairview, Canada 21806</p>
      <ul class="contact__list">
        <li>
          <svg viewBox="0 0 12 12" aria-hidden="true"><path d="M2.5 1l2 2.2-1 1.3c.7 1.5 1.8 2.6 3.2 3.2l1.3-1L10.2 8.5 9 10.5C5 10.2 1.8 7 1.5 3z" fill="#fff"/></svg>
          555-210-4418
        </li>
        <li>
          <svg viewBox="0 0 12 12" aria-hidden="true"><rect x="3" y="0.8" width="6" height="10.4" rx="1" fill="none" stroke="#fff" stroke-width="1.2"/></svg>
          555-310-7726
        </li>
        <li>
          <svg viewBox="0 0 12 12" aria-hidden="true"><rect x="0.8" y="2.3" width="10.4" height="7.4" fill="none" stroke="#fff" stroke-width="1.2"/><path d="M1 2.5l5 4 5-4" fill="none" stroke="#fff" stroke-width="1.2"/></svg>
          hello@meridiancare.com
        </li>
        <li>
          <svg viewBox="0 0 12 12" aria-hidden="true"><circle cx="6" cy="6" r="5" fill="none" stroke="#fff" stroke-width="1.2"/><path d="M1 6h10M6 1c-2.5 3-2.5 7 0 10M6 1c2.5 3 2.5 7 0 10" fill="none" stroke="#fff" stroke-width="1"/></svg>
          www.meridiancare.com
        </li>
      </ul>
    </div>
  </section>

  <section class="card card--front-blue" aria-label="Card front, blue">
    <div class="brand">
      <span class="brand__dot"></span>
      <span class="brand__name">Meridian Care Clinic</span>
    </div>
  </section>

</main>
</body>
</html>
```